A clean crisp business card for a Landscape Construction company. Designed to be easy to read contact/ info and also be appealing/interesting, unlike a traditional business card.

Industry/Entity Type

Landscape Construction

Contact Information for Business Card

Company name : Brambleford Landscape Construction, phone number: (877) 62Vista, website:Bramblefordyards.example, Email, sales@bramblefordyards.example

Requirements
Nice to have
• Luxurious finishes/ details…. Icons or emblems next to contact info
Should not have
• Clipart or general pictures

```html
<!DOCTYPE html>
<html lang="en">
<head>
<meta charset="utf-8">
<title>Brambleford Landscape Construction – Business Card</title>
<link rel="stylesheet" href="https://fonts.googleapis.com/css2?family=Jost:wght@400;500&family=Oswald:wght@500&display=swap">
<style>
  :root {
    --backdrop: #b9bdbf;
    --card: #f6f6f3;
    --edge-blue: #1f5a99;
    --brand-blue: #1b64c4;
    --brand-green: #7cc243;
    --logo-blue: #1d3f94;
    --ink: #4a4a4a;
    --muted: #6b6b6b;
  }
  * { box-sizing: border-box; margin: 0; padding: 0; }
  html, body { width: 1200px; height: 824px; overflow: hidden; }
  body {
    background: var(--backdrop);
    display: flex;
    align-items: center;
    justify-content: center;
    gap: 60px;
    font-family: "Jost", "Futura", sans-serif;
  }
  .card {
    width: 500px;
    height: 286px;
    background: var(--card);
    border-bottom: 6px solid var(--edge-blue);
    box-shadow: 0 10px 24px rgba(0, 0, 0, 0.18);
    display: flex;
    flex-direction: column;
    align-items: center;
    justify-content: center;
    text-align: center;
  }
  .contact-name {
    font-family: "Oswald", "Arial Narrow", sans-serif;
    font-weight: 500;
    font-size: 22px;
    letter-spacing: 0.5px;
    line-height: 1.1;
  }
  .contact-name .first { color: var(--brand-blue); }
  .contact-name .last { color: var(--brand-green); }
  .contact-title {
    font-size: 13px;
    color: var(--muted);
    margin: 2px 0 6px;
  }
  .contact-line {
    font-size: 14px;
    color: var(--ink);
    line-height: 1.45;
  }
  .brand {
    display: flex;
    align-items: center;
    gap: 12px;
  }
  .brand-mark {
    width: 22px;
    height: 22px;
    border-radius: 50%;
    background: var(--brand-green);
    flex: none;
  }
  .brand-name {
    font-family: "Jost", "Futura", sans-serif;
    font-weight: 500;
    font-size: 24px;
    color: var(--logo-blue);
    line-height: 1.2;
    text-align: left;
  }
</style>
</head>
<body>
  <section class="card card-front" aria-label="Contact side">
    <h1 class="contact-name"><span class="first">DANIEL</span> <span class="last">HARTLEY</span></h1>
    <p class="contact-title">President</p>
    <p class="contact-line">(877) 62Vista | sales@bramblefordyards.example</p>
    <p class="contact-line">www.Bramblefordyards.example</p>
  </section>

  <section class="card card-back" aria-label="Brand side">
    <div class="brand">
      <span class="brand-mark"></span>
      <p class="brand-name">Brambleford<br>Landscape Construction</p>
    </div>
  </section>
</body>
</html>
```